Business Card Design for Marketing Firm

Looking for business card design for higher end marketing firm. Clean but impressionable/trendy. We are a marketing firm that represents manufacturers in the foodservice equipment and supply industry. Our customers are end users such has hotels, restaurants, country clubs, convention centers and casinos as well as distributors of restaurants supplies and equipment, and manufacturers of foodservice equipment and supplies.
Target Market(s)
Hotels, Restaurants, Supply & Equipment Distributors, Foodservice Manufacturers
Industry/Entity Type
Foodservice/Hospitality
Contact Information for Business Card
Name, Title, Contact Number, Email, Website, Social Media, Address
Requirements
Must have
- Clean & Simple but Serious and Impressionable

```html
<!DOCTYPE html>
<html lang="en">
<head>
<meta charset="utf-8">
<title>Meridian Service Reps – Business Card</title>
<link href="https://fonts.googleapis.com/css2?family=Open+Sans:wght@400;700&display=swap" rel="stylesheet">
<style>
  :root {
    --navy: #272a78;
    --ink: #222222;
    --paper: #ffffff;
    --backdrop: #dcdcda;
    --shadow: rgba(0, 0, 0, 0.18);
  }
  html, body {
    margin: 0;
    width: 1200px;
    height: 801px;
    overflow: hidden;
    background: var(--backdrop);
  }
  .stage {
    width: 1200px;
    height: 801px;
    display: flex;
    align-items: center;
    justify-content: center;
    gap: 40px;
  }
  .card {
    position: relative;
    width: 530px;
    height: 303px;
    background: var(--paper);
    border-radius: 18px;
    border-bottom: 3px solid var(--navy);
    box-shadow: 0 10px 28px var(--shadow);
    box-sizing: border-box;
    overflow: hidden;
    font-family: "Open Sans", sans-serif;
  }

  /* Neutral brand name placeholder */
  .brand-name {
    display: flex;
    align-items: center;
    gap: 10px;
    color: var(--navy);
    font-weight: 700;
    white-space: nowrap;
  }
  .brand-name__mark {
    flex: none;
    border-radius: 50%;
    background: var(--navy);
  }

  /* Contact side */
  .card--contact .brand-name {
    position: absolute;
    left: 34px;
    top: 136px;
    font-size: 18px;
  }
  .card--contact .brand-name__mark { width: 22px; height: 22px; }
  .divider {
    position: absolute;
    left: 290px;
    top: 60px;
    width: 2px;
    height: 190px;
    background: var(--navy);
  }
  .contact {
    position: absolute;
    left: 310px;
    top: 58px;
    color: var(--navy);
  }
  .contact__name { font-weight: 700; font-size: 20px; letter-spacing: 0.3px; }
  .contact__title { font-size: 13px; color: var(--ink); margin-bottom: 12px; }
  .contact__line {
    display: flex;
    align-items: center;
    gap: 7px;
    font-size: 13px;
    color: var(--ink);
    margin-bottom: 3px;
  }
  .contact__line svg { width: 12px; height: 12px; flex: none; }
  .contact__address { font-size: 13px; color: var(--ink); margin-top: 12px; line-height: 1.35; }

  /* Brand side */
  .card--brand .brand-name {
    position: absolute;
    left: 0;
    right: 0;
    top: 110px;
    justify-content: center;
    font-size: 32px;
  }
  .card--brand .brand-name__mark { width: 34px; height: 34px; }
  .social {
    position: absolute;
    left: 0;
    right: 0;
    bottom: 48px;
    display: flex;
    justify-content: center;
    gap: 6px;
  }
  .social__dot {
    width: 18px;
    height: 18px;
    border-radius: 50%;
    background: var(--navy);
  }
</style>
</head>
<body>
<main class="stage">
  <section class="card card--contact">
    <div class="brand-name">
      <span class="brand-name__mark"></span>
      <span>Meridian Service Reps</span>
    </div>
    <div class="divider"></div>
    <div class="contact">
      <div class="contact__name">DANIEL HARPER</div>
      <div class="contact__title">Managing Director</div>
      <div class="contact__line">
        <svg viewBox="0 0 24 24" aria-hidden="true"><path fill="#272a78" d="M6.6 10.8a15 15 0 0 0 6.6 6.6l2.2-2.2a1 1 0 0 1 1-.25 11.4 11.4 0 0 0 3.6.6 1 1 0 0 1 1 1V20a1 1 0 0 1-1 1A17 17 0 0 1 3 4a1 1 0 0 1 1-1h3.5a1 1 0 0 1 1 1c0 1.25.2 2.45.6 3.6a1 1 0 0 1-.25 1z"/></svg>
        123 456 789
      </div>
      <div class="contact__line">
        <svg viewBox="0 0 24 24" aria-hidden="true"><rect x="2" y="5" width="20" height="14" rx="2" fill="#272a78"/><path d="M3 6l9 7 9-7" stroke="#fff" stroke-width="1.8" fill="none"/></svg>
        info@meridianreps.com
      </div>
      <div class="contact__line">
        <svg viewBox="0 0 24 24" aria-hidden="true"><circle cx="12" cy="12" r="10" fill="#272a78"/><path d="M2 12h20M12 2c3 3 3 17 0 20M12 2c-3 3-3 17 0 20" stroke="#fff" stroke-width="1.4" fill="none"/></svg>
        www.meridianreps.com
      </div>
      <div class="contact__address">Your address, City<br>State, Zip 1234</div>
    </div>
  </section>

  <section class="card card--brand">
    <div class="brand-name">
      <span class="brand-name__mark"></span>
      <span>Meridian Service Reps</span>
    </div>
    <div class="social" aria-label="Social media links">
      <span class="social__dot"></span>
      <span class="social__dot"></span>
      <span class="social__dot"></span>
      <span class="social__dot"></span>
      <span class="social__dot"></span>
      <span class="social__dot"></span>
    </div>
  </section>
</main>
</body>
</html>
```